New Business Card Design

We would like to refresh our business cards and make them look better. We are an IT company specialising in Cloud Services, IT Managed Services, software and hardware. I have attached a PSD of our current design. Also attached our logo.
Updates

I have uploaded all new logos in EPS format.

Can you please edit all designs to include a job title for Marcus Hollis, eg. General Manager

Industry/Entity Type

Software

Colors
ffffff

Requirements
Must have
• Please use white background.
Should not have
• Black background

```html
<!DOCTYPE html>
<html lang="en">
<head>
<meta charset="utf-8">
<title>Northvale Technology – Business Card</title>
<link rel="stylesheet" href="https://fonts.googleapis.com/css2?family=Open+Sans:wght@400;600;700&display=swap">
<style>
  :root {
    --backdrop: #e9e7e3;
    --card: #ffffff;
    --ink: #2e2e2e;
    --ink-soft: #4a4d52;
    --accent: #b7372b;
    --square-grey: #8d949c;
    --divider: #c9cdd2;
  }
  * { box-sizing: border-box; margin: 0; padding: 0; }
  html, body {
    width: 1200px; height: 720px; overflow: hidden;
    background: var(--backdrop);
    font-family: "Open Sans", Arial, sans-serif;
    color: var(--ink);
  }
  .canvas {
    width: 1200px; height: 720px;
    display: flex; align-items: center; justify-content: center; gap: 40px;
  }
  .card {
    position: relative;
    width: 540px; height: 310px;
    background: var(--card);
    border-radius: 3px;
    box-shadow: 0 2px 10px rgba(0,0,0,.12);
    overflow: hidden;
  }

  /* Contact side */
  .person {
    position: absolute; left: 30px; top: 112px; width: 200px; text-align: right;
  }
  .person-name { color: var(--accent); font-weight: 700; font-size: 23px; line-height: 1.2; }
  .person-title { font-size: 16px; color: var(--ink); margin-top: 2px; }
  .person-mobile {
    font-size: 16px; color: var(--ink-soft); margin-top: 10px;
    display: flex; justify-content: flex-end; align-items: center; gap: 10px;
  }
  .divider {
    position: absolute; left: 250px; top: 70px; width: 1px; height: 120px; background: var(--divider);
  }
  .contact-list {
    position: absolute; left: 268px; top: 72px; list-style: none;
  }
  .contact-list li {
    display: flex; align-items: center; gap: 10px;
    font-size: 15px; color: var(--ink-soft); height: 30px; white-space: nowrap;
  }
  .icon { width: 18px; height: 18px; flex: none; }

  /* Brand side */
  .brand {
    position: absolute; left: 0; right: 0; top: 100px;
    display: flex; align-items: center; justify-content: center; gap: 16px;
  }
  .brand-square { width: 36px; height: 36px; background: var(--square-grey); }
  .brand-name { font-size: 30px; font-weight: 600; color: var(--ink); line-height: 1.1; }
  .tagline {
    position: absolute; left: 0; right: 0; bottom: 56px;
    text-align: center; font-size: 17px; line-height: 1.45; color: var(--ink-soft);
  }
</style>
</head>
<body>
<main class="canvas">
  <section class="card card-front" aria-label="Business card, contact side">
    <div class="person">
      <p class="person-name">Marcus Hollis</p>
      <p class="person-title">General Manager</p>
      <p class="person-mobile">
        <svg class="icon" viewBox="0 0 18 18" aria-hidden="true"><rect x="5" y="1" width="8" height="16" rx="1.5" fill="var(--accent)"/><rect x="6.5" y="3" width="5" height="6" fill="#fff"/><g fill="#fff"><circle cx="7.2" cy="11.5" r=".8"/><circle cx="9" cy="11.5" r=".8"/><circle cx="10.8" cy="11.5" r=".8"/><circle cx="7.2" cy="13.6" r=".8"/><circle cx="9" cy="13.6" r=".8"/><circle cx="10.8" cy="13.6" r=".8"/></g></svg>
        0455 218 637
      </p>
    </div>
    <div class="divider" aria-hidden="true"></div>
    <ul class="contact-list">
      <li>
        <svg class="icon" viewBox="0 0 18 18" aria-hidden="true"><circle cx="9" cy="9" r="9" fill="var(--accent)"/><path d="M6 4.5l2 2.2-1.1 1.3c.6 1.3 1.6 2.3 2.9 2.9l1.3-1.1 2.2 2-1.2 1.7C8.9 13.5 4.5 9.1 4.5 5.9z" fill="#fff"/></svg>
        07 3650 1480
      </li>
      <li>
        <svg class="icon" viewBox="0 0 18 18" aria-hidden="true"><circle cx="9" cy="9" r="9" fill="var(--accent)"/><rect x="4.5" y="6" width="9" height="6.5" fill="#fff"/><path d="M4.5 6l4.5 3.6L13.5 6" fill="none" stroke="var(--accent)" stroke-width="1"/></svg>
        hollism@northvaleit.com.au
      </li>
      <li>
        <svg class="icon" viewBox="0 0 18 18" aria-hidden="true"><circle cx="9" cy="9" r="9" fill="var(--accent)"/><g fill="none" stroke="#fff" stroke-width="1"><circle cx="9" cy="9" r="5"/><ellipse cx="9" cy="9" rx="2.2" ry="5"/><path d="M4 9h10"/></g></svg>
        www.northvaleit.com.au
      </li>
    </ul>
  </section>

  <section class="card card-back" aria-label="Business card, brand side">
    <div class="brand">
      <span class="brand-square" aria-hidden="true"></span>
      <p class="brand-name">Northvale Technology</p>
    </div>
    <p class="tagline">We are an IT company specializing in Cloud Services<br>IT Managed Services, software and hardware</p>
  </section>
</main>
</body>
</html>
```